KELBRIDGE PAINTING

We are a painting company. We paint residential, commercial and strata jobs. I need the website to be very sharp, neat and elegant. I've attached our logo. the Logo needs to be embossed as a gold color and the background like a Matt black. I need these tabs:

• HOME • ABOUT US • SERVICES • TESTIMONIALS • SHOWCASE • CONTACT US

Be creative and innovative in your style.
take this as an example to just get the gist of what I'm expecting. If you can better it then the job is yours!

http://rickhalvorpainting.com.au/contact.html

I look forward to seeing your artwork :)

#These are the links to my logo in PSD format.

https://www.filevaultzy.com/s/qwertplk83nd7ha/Kelbridge%20Painting%20Luxury%20Gold.rar

https://www.filevaultzy.com/sh/bzuyrak2m5wqp9/QoPL7-xvMn

Painting

• Making the Logo embossed like the artworks i have attached is definitely a necessity.

Can you let me know if this is possible to apply to the website.

thank you

```html
<!DOCTYPE html>
<html lang="en">
<head>
<meta charset="utf-8">
<title>Kelbridge Painting – Showcase</title>
<link href="https://fonts.googleapis.com/css2?family=Source+Sans+3:ital,wght@0,400;0,600;0,700;1,400&display=swap" rel="stylesheet">
<style>
:root{
  --ink:#1d212b;
  --gold:#f2be3e;
  --gold-deep:#d9a520;
  --gold-mid:#e8b640;
  --gold-soft:#f0c870;
  --cream:#f5dcae;
  --slate-1:#3d434d;
  --slate-2:#5a6069;
  --slate-3:#8a8f98;
  --caption:#9a9ea6;
  --footer:#9b9ea5;
  --white:#ffffff;
}
*{margin:0;padding:0;box-sizing:border-box}
html,body{width:957px;height:1200px;overflow:hidden;background:var(--ink)}
body{font-family:"Source Sans 3",sans-serif;position:relative;color:var(--white)}
.abs{position:absolute}

.site-header{left:0;top:0;width:957px;height:74px;background:var(--ink);border-bottom:1px solid var(--gold-deep)}
.phone{left:692px;top:15px;font-size:17px;font-weight:700;color:var(--gold);display:flex;align-items:center;gap:6px}
.main-nav{left:342px;top:51px;display:flex;gap:24px;font-size:11.5px;font-weight:700;letter-spacing:.4px}
.main-nav a{color:var(--white);text-decoration:none}
.main-nav a.active{color:var(--gold)}

.brand-mark{left:134px;top:18px;width:92px;height:92px;border-radius:50%;background:var(--ink);border:3px solid var(--gold-deep);z-index:3}
.brand-strip{left:224px;top:74px;width:402px;height:32px;background:linear-gradient(90deg,var(--gold-deep),var(--gold) 60%,var(--cream));z-index:2;display:flex;align-items:center;padding-left:10px;color:var(--ink)}
.brand-name{font-size:17px;font-weight:700;letter-spacing:.6px}
.brand-sep{width:1px;height:16px;background:var(--ink);margin:0 11px}
.brand-tag{font-size:14px;font-style:italic}

.hero{left:0;top:74px;width:957px;height:360px;background:linear-gradient(180deg,#6e5540 0%,#5a3e2c 40%,#8a6b55 75%,#bfa896 100%)}
.slider-dots{left:773px;top:99px;display:flex;gap:6px}
.slider-dots span{width:7px;height:7px;background:var(--slate-1)}
.slider-dots span.on{background:var(--gold)}
.hero-accent-left{left:132px;top:266px;width:44px;height:45px;background:var(--gold-deep)}
.hero-accent-right{left:530px;top:312px;width:132px;height:82px;background:var(--gold-deep)}
.hero-card{left:140px;top:275px;width:508px;height:111px;background:var(--ink);padding:14px 28px;font-size:34px;line-height:40px}
.hero-tab{left:619px;top:275px;width:29px;height:5px;background:var(--slate-3)}

.stripe{height:7px;display:flex}
.stripe span{display:block;height:100%}

.showcase-title{left:132px;top:468px;font-size:35px;font-weight:700;color:var(--gold);letter-spacing:.5px}
.tile{width:191px;height:191px}
.tile-caption{width:191px;text-align:center;font-size:13px;font-weight:700;color:var(--caption);letter-spacing:.5px}

.site-footer{left:0;top:1067px;width:957px;height:133px;background:var(--footer);color:var(--ink)}
.brands-label{left:134px;top:21px;font-size:17px;line-height:16px;font-weight:400}
.brands-label small{display:block;font-size:12px;margin-top:3px}
.partner{top:30px;font-size:20px;font-weight:700;color:var(--ink)}
.copyright{left:134px;top:101px;font-size:10px}
.social{top:95px;width:24px;height:24px;border-radius:50%;background:var(--ink)}
</style>
</head>
<body>

<header class="site-header abs">
  <div class="phone abs">
    <svg width="16" height="16" viewBox="0 0 24 24" aria-hidden="true"><path fill="#f2be3e" d="M6.6 10.8a15 15 0 0 0 6.6 6.6l2.2-2.2a1 1 0 0 1 1-.25 11.4 11.4 0 0 0 3.6.57 1 1 0 0 1 1 1V20a1 1 0 0 1-1 1A17 17 0 0 1 3 4a1 1 0 0 1 1-1h3.5a1 1 0 0 1 1 1c0 1.25.2 2.45.57 3.6a1 1 0 0 1-.25 1z"/></svg>
    1300 47 19 52
  </div>
  <nav class="main-nav abs">
    <a href="#">HOME</a><a href="#">ABOUT US</a><a href="#">SERVICES</a><a href="#">TESTIMONIALS</a><a href="#" class="active">SHOWCASE</a><a href="#">CONTACT US</a>
  </nav>
</header>

<section class="hero abs" role="img" aria-label="Photo of a living room with a brown and cream sectional sofa"></section>
<div class="brand-mark abs"></div>
<div class="brand-strip abs"><span class="brand-name">KELBRIDGE PAINTING</span><span class="brand-sep"></span><span class="brand-tag">Painting Australia Everyday!</span></div>
<div class="slider-dots abs"><span></span><span></span><span></span><span class="on"></span></div>
<div class="hero-accent-left abs"></div>
<div class="hero-accent-right abs"></div>
<div class="hero-card abs">We paint residential,<br>commercial and strata jobs</div>
<div class="hero-tab abs"></div>

<div class="stripe abs" style="left:0;top:434px;width:957px">
  <span style="width:229px;background:var(--ink)"></span>
  <span style="width:65px;background:var(--slate-1)"></span>
  <span style="width:72px;background:var(--slate-2)"></span>
  <span style="width:114px;background:var(--slate-3)"></span>
  <span style="width:95px;background:var(--gold-deep)"></span>
  <span style="width:66px;background:var(--gold-mid)"></span>
  <span style="width:72px;background:var(--gold-soft)"></span>
  <span style="width:244px;background:var(--cream)"></span>
</div>

<main>
  <h1 class="showcase-title abs">Showcase</h1>

  <div class="tile abs" style="left:140px;top:552px;background:linear-gradient(160deg,#e9b928,#d8c7a8 60%,#f1efe8)" role="img" aria-label="Living room with yellow walls and white fireplace"></div>
  <div class="tile abs" style="left:382px;top:552px;background:linear-gradient(160deg,#8e6a3e,#9fb2a0 55%,#e8e4cf)" role="img" aria-label="Bedroom with padded headboard and pale green walls"></div>
  <div class="tile abs" style="left:626px;top:552px;background:linear-gradient(170deg,#ef9a2a,#c8793c 45%,#6a4a44)" role="img" aria-label="Lounge with orange feature wall and red chairs"></div>
  <p class="tile-caption abs" style="left:140px;top:756px">IMAGE TEXT</p>
  <p class="tile-caption abs" style="left:382px;top:756px">IMAGE TEXT</p>
  <p class="tile-caption abs" style="left:626px;top:756px">IMAGE TEXT</p>

  <div class="tile abs" style="left:140px;top:795px;background:linear-gradient(90deg,#8d8d8f 0%,#7b7b7d 48%,#f2c21a 52%,#e8b810 100%)" role="img" aria-label="Grey and yellow painted wall with mounted screen"></div>
  <div class="tile abs" style="left:382px;top:795px;background:linear-gradient(170deg,#c9b894,#b89a52 45%,#5e3e22)" role="img" aria-label="Open living area with ceiling fan and leather sofa"></div>
  <div class="tile abs" style="left:626px;top:795px;background:linear-gradient(160deg,#d8552a,#ea6a2e 50%,#f0b230)" role="img" aria-label="Bedroom with bright orange red walls"></div>
  <p class="tile-caption abs" style="left:140px;top:999px">IMAGE TEXT</p>
  <p class="tile-caption abs" style="left:382px;top:999px">IMAGE TEXT</p>
  <p class="tile-caption abs" style="left:626px;top:999px">IMAGE TEXT</p>
</main>

<div class="stripe abs" style="left:0;top:1060px;width:957px">
  <span style="width:243px;background:var(--cream)"></span>
  <span style="width:73px;background:var(--gold-mid)"></span>
  <span style="width:66px;background:var(--gold-soft)"></span>
  <span style="width:96px;background:var(--gold-deep)"></span>
  <span style="width:112px;background:var(--footer)"></span>
  <span style="width:72px;background:var(--slate-2)"></span>
  <span style="width:66px;background:var(--slate-1)"></span>
  <span style="width:229px;background:var(--footer)"></span>
</div>

<footer class="site-footer abs">
  <p class="brands-label abs">BRANDS<small>USED BY US</small></p>
  <span class="partner abs" style="left:252px">Corvane</span>
  <span class="partner abs" style="left:378px">Lustrel</span>
  <span class="partner abs" style="left:502px">Harwick</span>
  <span class="partner abs" style="left:682px">Endurite</span>
  <p class="copyright abs">Copyright @ 2013 Kelbridge Painting. All rights reserved.</p>
  <span class="social abs" style="left:689px"></span>
  <span class="social abs" style="left:726px"></span>
  <span class="social abs" style="left:762px"></span>
  <span class="social abs" style="left:799px"></span>
</footer>

</body>
</html>
```